Website for "Bright Morrow Ltd" cleaning bsuiness

We require a website to expose our business to the local market. We want to provide background on who we are and what we do but in an easily digestible way. We clean domestic and commercial premises and want to provide a list of all of our services to potential customers. We operate out of Warrington in the UK.

We would like the website to be animated in some way so that the experience of using it is not dull or mundane. This website needs to be an extension of our company.

Target Market(s)

30 - 60 year olds for Domestic plus commercial clients

Industry/Entity Type

Cleaning Service

Coding

Coded - Design and coding required

Number of Pages Required

4 page

Font styles to use
Sans Serif

Colors
0455a3
3176b5
85acd3
cfdeed
ffffff
000000
1b1b1b
c8c8c8
757575

Requirements
Must have
• Logo which has been provided. Theme based around the logo and its colours. Simple layout to avoid confusion.
Nice to have
• Animations where possible to impress the customer.
Should not have
• any pictures of cleaning equipment, fairies, maids etc

```html
<!DOCTYPE html>
<html lang="en">
<head>
<meta charset="utf-8">
<title>Bright Morrow Ltd – Professional Cleaning Service</title>
<link rel="stylesheet" href="https://fonts.googleapis.com/css2?family=Jost:wght@400;500&family=Open+Sans:wght@400;600&display=swap">
<style>
:root{
  --blue:#0455a3;
  --blue-mid:#3176b5;
  --blue-light:#85acd3;
  --blue-pale:#cfdeed;
  --white:#ffffff;
  --black:#000000;
  --ink:#1b1b1b;
  --grey-line:#c8c8c8;
  --grey-text:#757575;
  --footer:#2b2b2b;
  --footer-base:#1f1f1f;
}
*{box-sizing:border-box;margin:0;padding:0}
html,body{width:1200px;height:2200px;overflow:hidden;background:var(--white)}
body{position:relative;font-family:"Open Sans",Arial,sans-serif;color:var(--ink)}

/* header */
.site-header{position:absolute;left:0;top:0;width:1200px;height:115px;border-top:3px solid var(--blue);background:var(--white)}
.brand{position:absolute;left:135px;top:32px;display:flex;align-items:center;gap:10px;font-family:"Jost",Arial,sans-serif;font-weight:500;font-size:26px;color:var(--blue)}
.brand-mark{width:30px;height:30px;border-radius:50%;background:var(--blue)}
.top-contact{position:absolute;right:132px;top:22px;display:flex;gap:26px;font-size:12px;color:var(--grey-text)}
.top-contact span{display:flex;align-items:center;gap:8px}
.main-nav{position:absolute;top:76px;left:0;width:1200px;font-size:12px;color:var(--ink);text-transform:uppercase}
.main-nav a{position:absolute;color:inherit;text-decoration:none}
.main-nav a.active{color:var(--blue)}
.main-nav a.active::after{content:"";position:absolute;left:-6px;right:-6px;top:36px;height:3px;background:var(--blue)}

/* hero */
.hero{position:absolute;left:0;top:117px;width:1200px;height:443px;background:linear-gradient(180deg,#5e5a55 0%,#4b4f52 45%,#5a4c44 100%)}
.hero-title{position:absolute;top:110px;width:100%;text-align:center;font-family:"Jost",Arial,sans-serif;font-weight:500;font-size:60px;letter-spacing:1px;color:var(--white)}
.hero-sub{position:absolute;top:206px;width:100%;text-align:center;font-size:14px;color:var(--white)}
.btn-primary{position:absolute;left:481px;top:269px;width:238px;height:51px;background:var(--blue);color:var(--white);font-weight:600;font-size:14px;display:flex;align-items:center;justify-content:center;border-radius:2px}
.slider-dots{position:absolute;top:387px;left:571px;display:flex;gap:10px}
.slider-dots i{width:12px;height:12px;border-radius:50%;background:rgba(255,255,255,.4)}
.slider-dots i:first-child{background:var(--white)}

/* about */
.about-photo{position:absolute;left:59px;top:580px;width:420px;height:400px;background:radial-gradient(ellipse at 55% 45%,#e8c9a4 0%,#d9b58a 25%,#6fb3a5 55%,#f4f4f4 80%,#fff 100%)}
.section-title{font-family:"Jost",Arial,sans-serif;font-weight:400;font-size:35px;color:var(--blue)}
.about-title{position:absolute;left:491px;top:600px}
.about-text{position:absolute;left:491px;top:657px;width:580px;font-size:11px;line-height:19px;color:#444}
.feature{position:absolute;width:290px;height:80px}
.feature svg{position:absolute;left:0;top:0}
.feature h3{position:absolute;left:44px;top:0;font-family:"Jost",Arial,sans-serif;font-weight:400;font-size:19px;color:var(--ink);white-space:nowrap}
.feature p{position:absolute;left:44px;top:32px;width:240px;font-size:11px;line-height:19px;color:#555}

/* services */
.services{position:absolute;left:0;top:980px;width:1200px;height:467px;background:linear-gradient(180deg,#0a6ad0 0%,var(--blue) 100%);color:var(--white)}
.services .section-title{position:absolute;top:54px;width:100%;text-align:center;color:var(--white)}
.service{position:absolute;top:140px;width:270px;text-align:center}
.service .icon{height:58px;display:flex;align-items:center;justify-content:center}
.service h3{margin-top:32px;font-family:"Jost",Arial,sans-serif;font-weight:400;font-size:19px}
.service p{margin-top:18px;font-size:11px;line-height:19px}
.btn-outline{display:inline-block;margin-top:34px;width:101px;height:35px;line-height:33px;border:1px solid var(--white);border-radius:2px;font-size:11px}

/* testimonials */
.testimonials-title{position:absolute;top:1488px;width:100%;text-align:center}
.testimonials-intro{position:absolute;left:130px;top:1552px;width:940px;text-align:center;font-size:11px;line-height:19px;color:#555}
.testimonial{position:absolute;top:1631px;width:265px;text-align:center}
.avatar{width:80px;height:80px;border-radius:50%;margin:0 auto;background:radial-gradient(circle at 50% 45%,#d8a987 0%,#8a6a55 60%,#b9b9b9 100%)}
.testimonial p{margin-top:30px;font-size:10px;line-height:19px;color:#555}
.testimonial h4{margin-top:16px;font-family:"Open Sans",Arial,sans-serif;font-weight:400;font-size:14px;color:var(--blue)}

/* footer */
.site-footer{position:absolute;left:0;top:1893px;width:1200px;height:245px;background:var(--footer);color:#ddd}
.footer-brand{position:absolute;left:134px;top:78px;display:flex;align-items:center;gap:10px;font-family:"Jost",Arial,sans-serif;font-weight:500;font-size:23px;color:var(--white);white-space:nowrap}
.footer-brand .brand-mark{width:28px;height:28px;background:var(--white)}
.footer-col{position:absolute;top:34px}
.footer-col h5{font-family:"Jost",Arial,sans-serif;font-weight:400;font-size:14px;color:var(--white);letter-spacing:.5px;margin-bottom:16px}
.quick-links li{list-style:none;font-size:10px;line-height:21px;color:var(--white)}
.newsletter p{font-size:10px;color:#ccc}
.newsletter .field{margin-top:16px;width:196px;height:34px;background:#555;font-size:10px;line-height:34px;padding-left:10px;color:#eee}
.newsletter .subscribe{margin-top:17px;width:80px;height:30px;background:var(--blue);font-size:10px;line-height:30px;text-align:center;color:var(--white);border-radius:2px}
.contact-list li{list-style:none;display:flex;gap:12px;font-size:10px;line-height:14px;margin-bottom:13px;color:var(--white)}
.contact-list svg{flex:none;margin-top:1px}
.contact-list u{text-decoration:underline}
.footer-base{position:absolute;left:0;top:2138px;width:1200px;height:62px;background:var(--footer-base);color:#ddd;font-size:10px}
.footer-base .copy{position:absolute;left:132px;top:24px}
.social{position:absolute;right:140px;top:23px;display:flex;gap:12px}
.social i{width:13px;height:13px;border-radius:50%;background:#ddd}
</style>
</head>
<body>

<header class="site-header">
  <div class="brand"><span class="brand-mark"></span>Bright Morrow Ltd</div>
  <div class="top-contact">
    <span><svg width="11" height="11" viewBox="0 0 24 24"><path d="M6.6 10.8a15 15 0 0 0 6.6 6.6l2.2-2.2a1 1 0 0 1 1-.25 11.4 11.4 0 0 0 3.6.6 1 1 0 0 1 1 1V20a1 1 0 0 1-1 1A17 17 0 0 1 3 4a1 1 0 0 1 1-1h3.5a1 1 0 0 1 1 1c0 1.25.2 2.45.6 3.6a1 1 0 0 1-.25 1z" fill="#0455a3"/></svg>+44 (0)19 255 0182</span>
    <span><svg width="12" height="10" viewBox="0 0 24 18"><rect width="24" height="18" rx="2" fill="#0455a3"/><path d="M1 1l11 9 11-9" stroke="#fff" stroke-width="2" fill="none"/></svg>hello@brightmorrow-mail.com</span>
  </div>
  <nav class="main-nav">
    <a class="active" style="left:498px">Home</a>
    <a style="left:593px">About</a>
    <a style="left:696px">Services</a>
    <a style="left:809px">Gallery</a>
    <a style="left:919px">Blog</a>
    <a style="left:1015px">Contact</a>
  </nav>
</header>

<section class="hero" role="img" aria-label="Aerial photograph of a riverside city with a bridge">
  <h1 class="hero-title">CLEANING SERVICES</h1>
  <p class="hero-sub">WE CLEAN DOMESTIC AND COMMERCIAL PREMISES</p>
  <div class="btn-primary">REQUEST APPOINTMENT</div>
  <div class="slider-dots"><i></i><i></i><i></i></div>
</section>

<section class="about">
  <div class="about-photo" role="img" aria-label="Photograph of a smiling woman resting her head on her hand"></div>
  <h2 class="section-title about-title">WHO WE ARE</h2>
  <p class="about-text">Nemo enim ipsam voluptatem quia voluptas sit aspernatur aut odit aut fugit, sed quia consequuntur magni dolores eos qui ratione voluptatem sequi nesciunt. Neque porro quisquam est, qui dolorem ipsum quia dolor sit amet, consectetur, adipisci velit</p>

  <div class="feature" style="left:486px;top:752px">
    <svg width="26" height="34" viewBox="0 0 26 34" fill="none" stroke="#0455a3" stroke-width="1.6"><path d="M8 1h10l-2 9h-6z"/><circle cx="13" cy="22" r="10"/><circle cx="13" cy="22" r="5"/></svg>
    <h3>CERTIFICATION</h3>
    <p>Nemo enim ipsam voluptatem quia voluptas sit aspernatur</p>
  </div>
  <div class="feature" style="left:780px;top:752px">
    <svg width="32" height="30" viewBox="0 0 32 30" fill="none" stroke="#0455a3" stroke-width="1.6"><rect x="1" y="12" width="6" height="15"/><path d="M7 13l7-11c3 0 4 2 3 5l-1 5h10c2 0 3 2 2 4l-3 9c-1 2-2 2-4 2H7"/></svg>
    <h3>FAIR PRICES</h3>
    <p>Nemo enim ipsam voluptatem quia voluptas sit aspernatur</p>
  </div>
  <div class="feature" style="left:484px;top:856px">
    <svg width="32" height="32" viewBox="0 0 32 32" fill="none" stroke="#0455a3" stroke-width="1.6"><circle cx="16" cy="16" r="14.5"/><path d="M16 7v10h-7"/></svg>
    <h3 style="left:46px">24/7 OPENED</h3>
    <p style="left:46px">Nemo enim ipsam voluptatem quia voluptas sit aspernatur</p>
  </div>
  <div class="feature" style="left:780px;top:856px">
    <svg width="36" height="30" viewBox="0 0 36 30" fill="none" stroke="#0455a3" stroke-width="1.6"><circle cx="13" cy="9" r="6"/><path d="M2 28c0-7 5-11 11-11s11 4 11 11z"/><circle cx="24" cy="8" r="5"/><path d="M25 15c6 0 10 4 10 12h-9"/></svg>
    <h3>PROFESSIONAL STAFF</h3>
    <p>Nemo enim ipsam voluptatem quia voluptas sit aspernatur</p>
  </div>
</section>

<section class="services">
  <h2 class="section-title">WHAT WE DO</h2>
  <div class="service" style="left:128px">
    <div class="icon"><svg width="54" height="54" viewBox="0 0 54 54" fill="none" stroke="#fff" stroke-width="2"><path d="M48 6c-3-2-7 0-10 3L30 17 12 12l-5 4 15 9-8 9-6-1-3 3 8 4 4 8 3-3-1-6 9-8 9 15 4-5-5-18 8-8c3-3 5-7 3-10z"/></svg></div>
    <h3>DOMESTIC</h3>
    <p>Nemo enim ipsam voluptatem quia voluptas sit aspernatur aut odit aut fugit, sed quia consequuntur magni dolores eos</p>
    <span class="btn-outline">Read More</span>
  </div>
  <div class="service" style="left:465px">
    <div class="icon"><svg width="54" height="58" viewBox="0 0 54 58" fill="none" stroke="#fff" stroke-width="2"><rect x="12" y="2" width="30" height="11" rx="2"/><path d="M42 7h5v12H27v10"/><rect x="23" y="29" width="8" height="27" rx="1"/></svg></div>
    <h3>COMMERCIAL</h3>
    <p>Nemo enim ipsam voluptatem quia voluptas sit aspernatur aut odit aut fugit, sed quia consequuntur magni dolores eos</p>
    <span class="btn-outline">Read More</span>
  </div>
  <div class="service" style="left:804px">
    <div class="icon"><svg width="54" height="54" viewBox="0 0 54 54" fill="none" stroke="#fff" stroke-width="2"><path d="M23 3h8l1 6 5 2 5-4 6 6-4 5 2 5 6 1v8l-6 1-2 5 4 5-6 6-5-4-5 2-1 6h-8l-1-6-5-2-5 4-6-6 4-5-2-5-6-1v-8l6-1 2-5-4-5 6-6 5 4 5-2z"/><circle cx="27" cy="27" r="8"/></svg></div>
    <h3>POTENTIAL</h3>
    <p>Nemo enim ipsam voluptatem quia voluptas sit aspernatur aut odit aut fugit, sed quia consequuntur magni dolores eos</p>
    <span class="btn-outline">Read More</span>
  </div>
</section>

<section class="testimonials">
  <h2 class="section-title testimonials-title">WHAT CLIENT SAY</h2>
  <p class="testimonials-intro">Nemo enim ipsam voluptatem quia voluptas sit aspernatur aut odit aut fugit, sed quia consequuntur magni dolores eos qui ratione voluptatem sequi nesciunt. Neque porro quisquam est, qui dolorem ipsum quia dolor sit amet, consectetur, adipisci velit</p>
  <div class="testimonial" style="left:130px">
    <div class="avatar" role="img" aria-label="Portrait photograph of a client"></div>
    <p>Nemo enim ipsam voluptatem quia voluptas sit aspernatur aut odit aut fugit, sed quia consequuntur magni dolores eos qui ratione voluptatem</p>
    <h4>John Doe</h4>
  </div>
  <div class="testimonial" style="left:468px">
    <div class="avatar" role="img" aria-label="Portrait photograph of a client"></div>
    <p>Nemo enim ipsam voluptatem quia voluptas sit aspernatur aut odit aut fugit, sed quia consequuntur magni dolores eos qui ratione voluptatem</p>
    <h4>John Doe</h4>
  </div>
  <div class="testimonial" style="left:806px">
    <div class="avatar" role="img" aria-label="Portrait photograph of a client"></div>
    <p>Nemo enim ipsam voluptatem quia voluptas sit aspernatur aut odit aut fugit, sed quia consequuntur magni dolores eos qui ratione voluptatem</p>
    <h4>John Doe</h4>
  </div>
</section>

<footer class="site-footer">
  <div class="footer-brand"><span class="brand-mark"></span>Bright Morrow Ltd</div>
  <div class="footer-col" style="left:422px">
    <h5>QUICK LINKS</h5>
    <ul class="quick-links"><li>Home</li><li>About</li><li>Services</li><li>Gallery</li><li>Blog</li><li>Contact</li></ul>
  </div>
  <div class="footer-col newsletter" style="left:603px">
    <h5>NEWSLETTER</h5>
    <p>Sign Up for Our Newsletter &amp; Promotion</p>
    <div class="field">Enter Your email Id</div>
    <div class="subscribe">SUBSCRIBE</div>
  </div>
  <div class="footer-col" style="left:876px">
    <h5>CONTACT US</h5>
    <ul class="contact-list">
      <li><svg width="12" height="11" viewBox="0 0 24 22"><path d="M2 8c0-4 20-4 20 0v3h-5V8H7v3H2z M5 12h14l3 9H2z" fill="#fff"/></svg>+44 (0)19 255 0147</li>
      <li><svg width="12" height="11" viewBox="0 0 24 22"><rect x="5" y="1" width="14" height="6" fill="#fff"/><rect x="1" y="8" width="22" height="9" rx="2" fill="#fff"/><rect x="6" y="15" width="12" height="6" fill="#fff"/></svg>+44 (0)19 255 0147</li>
      <li><svg width="12" height="10" viewBox="0 0 24 18"><rect width="24" height="18" rx="2" fill="#fff"/><path d="M1 1l11 9 11-9" stroke="#2b2b2b" stroke-width="2" fill="none"/></svg><u>hello@brightmorrow-mail.com</u></li>
      <li><svg width="12" height="14" viewBox="0 0 20 26"><path d="M10 0a9 9 0 0 0-9 9c0 7 9 17 9 17s9-10 9-17a9 9 0 0 0-9-9zm0 12a3 3 0 1 1 0-6 3 3 0 0 1 0 6z" fill="#fff"/></svg>#2868 Lorem ipsum dolor sit amet,<br>consectetur adipiscing</li>
    </ul>
  </div>
</footer>

<div class="footer-base">
  <p class="copy">Copyright © 2016 Brightmorrow. All Right Reserved.</p>
  <div class="social" aria-label="Social media links"><i></i><i></i><i></i><i></i><i></i></div>
</div>

</body>
</html>
```